Professional Engineering Web Design

Project Brief: Website Redesign for Mechanical Design Consultancy
Project Overview
I want to update and improve my current website to create a more professional, modern, and high-credibility online presence for my mechanical design consultancy.

Current site: https://valtorix.design/

The new website must communicate expertise, precision, and trust—matching the standard of top engineering and product design agencies.

Reference Websites (Style + Structure Inspiration)
These represent the quality, cleanliness, and professionalism I want to achieve:

https://plinthwaredesign.com/
https://www.sorvane.com/
https://bramlow-uk.com/
Brand Look
Professional, modern, engineering-focused aesthetic
Clean layouts and strong typography
High-quality imagery conveying precision, innovation, and mechanical expertise
Colour scheme and styling must follow my existing logo (attached in project)
Platform Requirements
The website must be built on WordPress
Should use a clean, flexible theme or modern page builder (Elementor, Gutenberg, Bricks, or similar)
Avoid overly complex custom coding so I can easily edit content later
Final deliverable must allow me to manage and update content without developer assistance
Functionality
Fast-loading, lightweight, and smooth user experience
Clean animations and transitions similar to the reference sites
Fully mobile responsive
Clear navigation and strong visual hierarchy
Contact forms optimised for lead generation
Optional: subtle scroll effects, case study sliders, icon animations, etc.
SEO Aspirations
Developer should recommend and implement a modern SEO strategy
Proper on-page SEO setup (titles, meta, schema, alt tags, heading structure)
Optimised site architecture for ranking and crawling
Aim: Generate leads through improved visibility and keyword targeting
Optional but useful: Google Analytics, Google Search Console setup
User Journeys
(Recommended structure)

The site should be crafted around clear, intuitive journeys for each type of visitor:

Potential new clients
Quickly understand what services I offer
View examples of past work / case studies
See credibility indicators (process, expertise, industries served)
Easily contact me or request a project discussion
Returning clients
Access updated portfolio items
Find contact details or book follow-up work easily
General visitors discovering through SEO
Be guided to valtorix service areas
Understand my value proposition quickly
Be invited to learn more or make contact
The developer should design the structure to support these journeys smoothly.

Maintenance Expectations
Website will be maintained by me, so it should be easy to update using relatively basic WordPress skills
Use modular templates and simple backend structure
Avoid unnecessary plugins
Provide brief handover documentation if required
Hosting Preferences
Site is currently hosted via a family member
Open to discussing moving to a paid, reliable hosting provider if preferable for performance and maintainability
Developer may advise on the best hosting setup for WordPress
Content
Most content can be taken from the existing website
Developer is welcome to suggest improvements to structure, layout, and imagery
Must remain easy for me to edit or add new content later (e.g., new projects)
Deliverables
Fully built WordPress website
Clean, professional, modern design inspired by the reference sites
Mobile-responsive across all devices
SEO-ready structure and optimisations
Transfer of website and admin rights
Any design assets, templates, or documentation used

```html
<!DOCTYPE html>
<html lang="en">
<head>
<meta charset="utf-8">
<title>Valtorix Mechanical Design</title>
<link rel="stylesheet" href="https://fonts.googleapis.com/css2?family=Montserrat:wght@700;800&family=Manrope:wght@400;500;600;700&display=swap">
<style>
:root{
  --blue:#2c55f2;
  --blue-dark:#2149e0;
  --ink:#16181d;
  --text:#2b2e35;
  --muted:#6b7079;
  --faint:#c3c7ce;
  --line:#e7e9ee;
  --grey-bg:#f4f5f8;
  --white:#ffffff;
}
*{margin:0;padding:0;box-sizing:border-box}
html,body{width:1200px;height:3125px;overflow:hidden;background:var(--white)}
body{font-family:"Manrope",sans-serif;color:var(--text);position:relative}
.abs{position:absolute}
.heading{font-family:"Montserrat",sans-serif;font-weight:800;color:var(--ink)}
.accent{color:var(--blue)}

/* header */
.site-header{position:absolute;top:0;left:0;width:1200px;height:76px;background:var(--white)}
.brand{position:absolute;left:143px;top:14px;display:flex;align-items:center;gap:10px}
.brand-dot{width:48px;height:48px;border-radius:50%;background:var(--blue)}
.brand-name{font-family:"Manrope",sans-serif;font-weight:700;font-size:26px;color:var(--blue);letter-spacing:1px}
.main-nav a{position:absolute;top:29px;font-size:14px;color:var(--ink);text-decoration:none;transform:translateX(-50%);font-weight:500}
.main-nav a.current{color:var(--blue)}
.search-icon{position:absolute;left:1041px;top:31px}

/* hero */
.hero{position:absolute;top:76px;left:0;width:1200px;height:562px;overflow:hidden}
.hero-visual{position:absolute;inset:0;background:linear-gradient(100deg,#1c1f24 0%,#2a2e34 40%,#4a4f56 68%,#2d3137 100%)}
.hero-title{position:absolute;left:140px;top:130px;font-family:"Montserrat",sans-serif;font-weight:800;font-size:60px;line-height:73px;color:var(--white)}
.hero-sub{position:absolute;left:143px;top:300px;font-size:19px;color:var(--white);font-weight:500}
.btn{display:inline-flex;align-items:center;gap:12px;background:var(--blue);color:var(--white);border-radius:26px;font-weight:700;text-decoration:none}
.hero .btn{position:absolute;left:143px;top:365px;height:48px;padding:0 22px;font-size:16px}
.scroll-cue{position:absolute;left:591px;top:503px}

/* expertise */
.expertise-visual{position:absolute;left:0;top:724px;width:576px;height:485px;border-radius:0 8px 8px 0;background:linear-gradient(135deg,#9fb0c2 0%,#5f7388 45%,#2b3644 100%)}
.section-title{font-size:38px;position:absolute}
.timeline{position:absolute;left:644px;top:880px;width:2px;height:190px;background:linear-gradient(var(--blue),rgba(44,85,242,0))}
.timeline-dot{position:absolute;left:636px;top:881px;width:18px;height:18px;border-radius:50%;background:var(--blue);box-shadow:0 0 0 4px rgba(44,85,242,.2)}
.service{position:absolute;left:680px;width:374px;height:126px;padding:22px 20px 0 85px}
.service svg{position:absolute;left:24px;top:24px}
.service h3{font-size:18px;font-weight:500;margin-bottom:10px}
.service p{font-size:13.5px;line-height:23px}
.service.active{background:var(--blue);border-radius:4px;color:var(--white)}
.service.mid{color:var(--muted);border-bottom:1px solid var(--line)}
.service.mid h3{color:#4b4f57}
.service.dim{color:var(--faint)}

/* about */
.about-title{left:0;width:1200px;text-align:center;top:1277px}
.about-intro{position:absolute;left:140px;width:920px;top:1341px;text-align:center;font-size:16.5px;line-height:29px;color:var(--ink)}
.portrait{position:absolute;left:143px;top:1435px;width:457px;height:385px;border-radius:8px;background:linear-gradient(135deg,#8b9a86 0%,#b9a48d 45%,#2f3a52 100%)}
.bio-card{position:absolute;left:600px;top:1475px;width:456px;height:265px;background:var(--white);box-shadow:0 10px 40px rgba(20,30,60,.08);padding:28px 42px 0 34px}
.bio-card h3{font-size:18px;font-weight:500;line-height:28px;color:var(--ink);margin-bottom:14px}
.bio-card p{font-size:13.5px;line-height:24px;color:var(--muted);text-align:justify}
.bio-btn{position:absolute;left:634px;top:1723px;height:45px;padding:0 24px;font-size:14px}

/* works */
.works{position:absolute;left:0;top:1900px;width:1200px;height:603px;background:var(--grey-bg)}
.works-title{left:0;width:1200px;text-align:center;top:50px}
.works-sub{position:absolute;left:0;width:1200px;text-align:center;top:115px;font-size:18px;color:var(--muted)}
.work-card{position:absolute;top:166px;width:289px;height:360px;background:var(--white);text-align:center}
.work-img{height:208px}
.work-card h3{font-size:16.5px;font-weight:500;color:var(--ink);margin:20px 0 12px}
.work-card p{font-size:13.5px;line-height:23px;color:var(--muted);padding:0 22px}
.learn{display:inline-flex;align-items:center;gap:10px;margin-top:15px;font-size:14.5px;font-weight:500;color:var(--blue)}
.slider-arrow{position:absolute;top:360px}

/* feedback */
.feedback{position:absolute;left:0;top:2503px;width:1200px;height:367px;background:var(--blue);color:var(--white)}
.feedback h2{position:absolute;left:142px;top:46px;font-family:"Montserrat",sans-serif;font-weight:800;font-size:37px;line-height:52px}
.round-btn{position:absolute;top:232px;width:44px;height:44px;border-radius:50%;display:flex;align-items:center;justify-content:center}
.round-btn.prev{left:144px;border:1.5px solid rgba(255,255,255,.8)}
.round-btn.next{left:200px;background:var(--white)}
.avatar{position:absolute;left:672px;top:57px;width:72px;height:72px;border-radius:50%;background:linear-gradient(160deg,#d8dde6,#8a95a6)}
.stars{position:absolute;left:672px;top:148px;display:flex;gap:3px}
.quote{position:absolute;left:672px;top:180px;width:400px;font-size:13px;line-height:24px}
.client{position:absolute;left:671px;top:288px;font-size:17px;font-weight:500}
.client span{font-size:11px;margin-left:8px}

/* footer */
.site-footer{position:absolute;left:0;top:2870px;width:1200px;height:255px}
.footer-cta{position:absolute;left:143px;top:72px;font-size:24px;line-height:40px;color:#555a63;font-weight:500}
.footer-btn{position:absolute;left:143px;top:168px;height:43px;padding:0 24px;font-size:15px}
.footer-brand{position:absolute;left:0;width:1200px;top:80px;display:flex;flex-direction:column;align-items:center;gap:8px}
.footer-brand .brand-dot{width:60px;height:60px}
.footer-brand .brand-name{font-size:30px}
.copyright{position:absolute;left:0;width:1200px;text-align:center;top:222px;font-size:13px;color:var(--muted)}
.contact-block{position:absolute;left:877px;top:72px}
.contact-block h4{font-size:15.5px;font-weight:500;color:var(--ink);margin-bottom:12px}
.contact-row{display:flex;gap:12px;font-size:13.5px;color:#4b4f57;line-height:22px;margin-bottom:10px}
.contact-icon{width:22px;height:22px;border-radius:50%;border:1px solid #c9d2f5;display:flex;align-items:center;justify-content:center;flex:none}
</style>
</head>
<body>

<header class="site-header">
  <div class="brand"><span class="brand-dot"></span><span class="brand-name">valtorix</span></div>
  <nav class="main-nav">
    <a href="#" class="current" style="left:570px">HOME</a>
    <a href="#" style="left:687px">PORTFOLIO</a>
    <a href="#" style="left:819px">SERVICES</a>
    <a href="#" style="left:946px">CONTACT</a>
  </nav>
  <svg class="search-icon" width="14" height="14" viewBox="0 0 14 14"><circle cx="6" cy="6" r="4.3" fill="none" stroke="#16181d" stroke-width="2"/><line x1="9.2" y1="9.2" x2="13" y2="13" stroke="#16181d" stroke-width="2.2"/></svg>
</header>

<section class="hero">
  <div class="hero-visual" role="img" aria-label="3D printer nozzle printing a grey lattice part in a dark workshop"></div>
  <h1 class="hero-title">Mechanical CAD<br>Design</h1>
  <p class="hero-sub">Cutting Edge Engineering</p>
  <a href="#" class="btn">Get Started <svg width="14" height="10" viewBox="0 0 14 10"><path d="M1 5h11M8 1l4 4-4 4" fill="none" stroke="#fff" stroke-width="1.6"/></svg></a>
  <svg class="scroll-cue" width="18" height="40" viewBox="0 0 18 40"><rect x="2" y="1" width="14" height="24" rx="7" fill="none" stroke="#fff" stroke-width="1.6"/><line x1="9" y1="6" x2="9" y2="11" stroke="#fff" stroke-width="1.6"/><path d="M9 29v9M6 35l3 3 3-3" fill="none" stroke="#fff" stroke-width="1.4"/></svg>
</section>

<section class="expertise">
  <div class="expertise-visual" role="img" aria-label="Engineer reviewing a 3D model on a tablet beside a desktop 3D printer"></div>
  <h2 class="heading section-title" style="left:635px;top:750px"><span class="accent">Our</span> Expertise</h2>
  <div class="timeline"></div><div class="timeline-dot"></div>
  <div class="service active" style="top:826px">
    <svg width="42" height="46" viewBox="0 0 42 46"><rect x="4" y="2" width="26" height="34" rx="2" fill="none" stroke="#fff" stroke-width="1.8"/><path d="M10 11h14M10 17h14M10 23h8" stroke="#fff" stroke-width="1.8"/><path d="M22 38l8-8 8 6-8 8z" fill="none" stroke="#fff" stroke-width="1.8"/></svg>
    <h3>Bespoke Product Design</h3>
    <p>Innovative design from concept through<br>the full development life cycle</p>
  </div>
  <div class="service mid" style="top:952px">
    <svg width="44" height="46" viewBox="0 0 44 46"><path d="M22 3l17 9v21l-17 10L5 33V12z M5 12l17 10 17-10 M22 22v21" fill="none" stroke="#9aa0a8" stroke-width="1.6"/></svg>
    <h3>3D Modelling and Drawings</h3>
    <p>We create 3D CAD, 2D engineering drawings<br>and photorealistic renders</p>
  </div>
  <div class="service dim" style="top:1078px">
    <svg width="46" height="46" viewBox="0 0 46 46"><circle cx="23" cy="23" r="15" fill="none" stroke="#d3d6db" stroke-width="1.6"/><circle cx="23" cy="23" r="6" fill="none" stroke="#d3d6db" stroke-width="1.6"/><path d="M23 3v6M23 37v6M3 23h6M37 23h6M9 9l4 4M33 33l4 4M37 9l-4 4M9 37l4-4" stroke="#d3d6db" stroke-width="1.6"/></svg>
    <h3>Design for Manufacture</h3>
    <p>Creating designs optimised for prototype<br>and production manufacture</p>
  </div>
</section>

<section class="about">
  <h2 class="heading section-title about-title"><span class="accent">About</span> Valtorix Mechanical Design</h2>
  <p class="about-intro">Welcome to Valtorix Mechanical Design. We are a UK based design consultancy offering a comprehensive mechanical and product design service from initial concepts through to full volume production.</p>
  <div class="portrait" role="img" aria-label="Portrait photo of the chief engineer"></div>
  <div class="bio-card">
    <h3>Rowan Hale is the Chief Engineer at Valtorix Mechanical Design.</h3>
    <p>He has 11 years experience working as a mechanical design engineer in multiple industries including high performance automotive, consumer products, medical, industrial plus many more. He has worked in multiple roles across a wide range of products.</p>
  </div>
  <a href="#" class="btn bio-btn">TELL US ABOUT YOUR IDEAS <svg width="14" height="10" viewBox="0 0 14 10"><path d="M1 5h11M8 1l4 4-4 4" fill="none" stroke="#fff" stroke-width="1.6"/></svg></a>
</section>

<section class="works">
  <h2 class="heading section-title works-title"><span class="accent">Our</span> Works</h2>
  <p class="works-sub">A Small Selection of Our Previous Projects</p>
  <svg class="slider-arrow" style="left:104px" width="14" height="24" viewBox="0 0 14 24"><path d="M12 2L2 12l10 10" fill="none" stroke="#16181d" stroke-width="2.2"/></svg>
  <svg class="slider-arrow" style="left:1082px" width="14" height="24" viewBox="0 0 14 24"><path d="M2 2l10 10-10 10" fill="none" stroke="#16181d" stroke-width="2.2"/></svg>
  <article class="work-card" style="left:143px">
    <div class="work-img" role="img" aria-label="Render of a three-piece alloy wheel" style="background:radial-gradient(circle at 45% 50%,#c9ccd1,#e9eaec 70%)"></div>
    <h3>3-Piece Alloy Wheels</h3>
    <p>We have been working on a long term project to bring custom 3-piece</p>
    <span class="learn">LEARN MORE <svg width="14" height="10" viewBox="0 0 14 10"><path d="M1 5h11M8 1l4 4-4 4" fill="none" stroke="#2c55f2" stroke-width="1.6"/></svg></span>
  </article>
  <article class="work-card" style="left:456px">
    <div class="work-img" role="img" aria-label="Render of a go-kart simulator rig" style="background:radial-gradient(circle at 50% 55%,#b5b8bd,#ececee 70%)"></div>
    <h3>Go-Kart Simulator Design</h3>
    <p>Our client already had an existing product, but wanted it updating</p>
    <span class="learn">LEARN MORE <svg width="14" height="10" viewBox="0 0 14 10"><path d="M1 5h11M8 1l4 4-4 4" fill="none" stroke="#2c55f2" stroke-width="1.6"/></svg></span>
  </article>
  <article class="work-card" style="left:767px">
    <div class="work-img" role="img" aria-label="Render of a camera mount on a threaded rail" style="background:radial-gradient(circle at 40% 50%,#c7b37a,#eceae4 65%)"></div>
    <h3>Lorem ipsum Dolor</h3>
    <p>Lorem ipsum dolor sit amet, consectetur adipiscing elit, sed do eiusmod</p>
    <span class="learn">LEARN MORE <svg width="14" height="10" viewBox="0 0 14 10"><path d="M1 5h11M8 1l4 4-4 4" fill="none" stroke="#2c55f2" stroke-width="1.6"/></svg></span>
  </article>
</section>

<section class="feedback">
  <h2>Feedback From<br>Some of Our Recent<br>Customers</h2>
  <span class="round-btn prev"><svg width="16" height="10" viewBox="0 0 16 10"><path d="M15 5H2M6 1L2 5l4 4" fill="none" stroke="#fff" stroke-width="1.5"/></svg></span>
  <span class="round-btn next"><svg width="16" height="10" viewBox="0 0 16 10"><path d="M1 5h13M10 1l4 4-4 4" fill="none" stroke="#16181d" stroke-width="1.5"/></svg></span>
  <div class="avatar" role="img" aria-label="Client portrait photo"></div>
  <div class="stars">
    <svg width="15" height="15" viewBox="0 0 24 24"><path d="M12 2l3 7 7 .6-5.4 4.7 1.7 7.2L12 17.8 5.7 21.5l1.7-7.2L2 9.6 9 9z" fill="#ffc21a"/></svg>
    <svg width="15" height="15" viewBox="0 0 24 24"><path d="M12 2l3 7 7 .6-5.4 4.7 1.7 7.2L12 17.8 5.7 21.5l1.7-7.2L2 9.6 9 9z" fill="#ffc21a"/></svg>
    <svg width="15" height="15" viewBox="0 0 24 24"><path d="M12 2l3 7 7 .6-5.4 4.7 1.7 7.2L12 17.8 5.7 21.5l1.7-7.2L2 9.6 9 9z" fill="#ffc21a"/></svg>
    <svg width="15" height="15" viewBox="0 0 24 24"><path d="M12 2l3 7 7 .6-5.4 4.7 1.7 7.2L12 17.8 5.7 21.5l1.7-7.2L2 9.6 9 9z" fill="#ffc21a"/></svg>
    <svg width="15" height="15" viewBox="0 0 24 24"><path d="M12 2l3 7 7 .6-5.4 4.7 1.7 7.2L12 17.8 5.7 21.5l1.7-7.2L2 9.6 9 9z" fill="#ffc21a"/></svg>
  </div>
  <p class="quote">"Rowan's description of his abilities was accurate. He is very capable and responsive. He worked very quickly and efficiently, cheerfully incorporating suggestions and revisions within a short time frame. I have no hesitation in recommending Rowan to anyone ...</p>
  <p class="client">Alistair Brenner<span>(Client)</span></p>
</section>

<footer class="site-footer">
  <p class="footer-cta">Curious What Else<br>We Do?</p>
  <a href="#" class="btn footer-btn">See Here <svg width="14" height="10" viewBox="0 0 14 10"><path d="M1 5h11M8 1l4 4-4 4" fill="none" stroke="#fff" stroke-width="1.6"/></svg></a>
  <div class="footer-brand"><span class="brand-dot"></span><span class="brand-name">valtorix</span></div>
  <p class="copyright">© 2025 Valtorix Mechanical Design</p>
  <div class="contact-block">
    <h4>GET IN TOUCH</h4>
    <div class="contact-row"><span class="contact-icon"><svg width="11" height="11" viewBox="0 0 24 24"><path d="M6 2l4 5-2 3c1 2 4 5 6 6l3-2 5 4-2 4C11 22 2 13 2 4z" fill="#2c55f2"/></svg></span>+44 (0) 7700 900482</div>
    <div class="contact-row"><span class="contact-icon"><svg width="11" height="9" viewBox="0 0 22 16"><rect x="1" y="1" width="20" height="14" rx="2" fill="#2c55f2"/><path d="M2 2l9 7 9-7" fill="none" stroke="#fff" stroke-width="1.6"/></svg></span>info@valtorix.design</div>
    <div class="contact-row"><span class="contact-icon"><svg width="10" height="12" viewBox="0 0 20 26"><path d="M10 1a8 8 0 0 1 8 8c0 6-8 16-8 16S2 15 2 9a8 8 0 0 1 8-8z" fill="none" stroke="#2c55f2" stroke-width="2.4"/><circle cx="10" cy="9" r="3" fill="#2c55f2"/></svg></span>CF10 4QT Harbour Works Rd,<br>Cardiff, UK</div>
  </div>
</footer>

</body>
</html>
```